Opening a Hair Salon

Looking for a design for my sign that looks high end, an emphasis on color but welcoming to men and women.

The name is Corvane Haircuts and Colors

Trying capture a more affluent client. Looking for a very modern look.

Reason: Time is going to quick and would like to see a few more options.

```html
<!DOCTYPE html>
<html lang="en">
<head>
<meta charset="utf-8">
<title>Corvane Haircuts and Colors – Storefront Sign</title>
<link rel="stylesheet" href="https://fonts.googleapis.com/css2?family=Ubuntu:wght@500;700&display=swap">
<style>
  :root {
    --backdrop: #e9e7e4;
    --sign-orange: #c2650f;
    --sign-orange-deep: #a9560a;
    --sign-glow: #f6d9a8;
    --ink-navy: #1b1c5c;
    --halo-white: rgba(255, 255, 255, 0.95);
  }

  * { margin: 0; padding: 0; box-sizing: border-box; }

  html, body {
    width: 1200px;
    height: 900px;
    overflow: hidden;
    background: var(--backdrop);
  }

  .canvas {
    position: relative;
    width: 1200px;
    height: 900px;
    display: flex;
    align-items: center;
    justify-content: center;
  }

  .sign {
    position: relative;
    width: 1060px;
    height: 340px;
    background:
      radial-gradient(ellipse 340px 190px at 68% 50%, var(--sign-glow) 0%, rgba(246, 217, 168, 0.55) 35%, rgba(194, 101, 15, 0) 100%),
      linear-gradient(180deg, var(--sign-orange) 0%, var(--sign-orange-deep) 100%);
  }

  .sign__phone {
    position: absolute;
    left: 48px;
    top: 178px;
    font-family: "Ubuntu", sans-serif;
    font-weight: 700;
    font-size: 60px;
    line-height: 1;
    letter-spacing: 1px;
    color: var(--ink-navy);
    white-space: nowrap;
    text-shadow:
      0 0 6px var(--halo-white),
      0 0 14px var(--halo-white),
      0 0 22px rgba(255, 255, 255, 0.7);
  }

  .brand {
    position: absolute;
    left: 470px;
    top: 62px;
    display: flex;
    flex-direction: column;
    align-items: flex-end;
    color: var(--ink-navy);
    font-family: "Ubuntu", sans-serif;
    font-weight: 700;
    white-space: nowrap;
  }

  .brand__name {
    font-size: 132px;
    line-height: 1;
    letter-spacing: -1px;
  }

  .brand__services {
    margin-top: 14px;
    font-size: 34px;
    line-height: 1;
    letter-spacing: 1px;
    text-transform: uppercase;
  }
</style>
</head>
<body>
  <main class="canvas">
    <section class="sign" aria-label="Corvane Haircuts and Colors storefront sign">
      <p class="sign__phone">4820 3917</p>
      <div class="brand">
        <span class="brand__name">Corvane</span>
        <span class="brand__services">Haircuts &amp; Colors</span>
      </div>
    </section>
  </main>
</body>
</html>
```